Vantrel Activated Carbon (coal-based)

The packaging for granular activated carbon must have a simple industrial concept but looks classy. Industrial look, bold and credible, also eye catching. Weight: 25 kg

Target Market(s)

Industrial

Industry/Entity Type

Water Treatment Industry

Requirements
Must have
• Weight : 25 kg, must have "coal-based", warning symbol in packaging
Nice to have
• There is a picture of granular activated carbon (coal-based) on the package

```html
<!DOCTYPE html>
<html lang="en">
<head>
<meta charset="utf-8">
<title>Vantrel Activated Carbon – 25 kg Bag</title>
<link href="https://fonts.googleapis.com/css2?family=Montserrat:wght@800;900&family=Poppins:wght@400;500;600;700&family=Barlow+Condensed:wght@300;400&display=swap" rel="stylesheet">
<style>
  :root {
    --stage: #f27d34;
    --stage-light: #f39a3f;
    --ink: #0b0b0b;
    --bag: #141414;
    --orange: #f26a2a;
    --orange-soft: #f58a4e;
    --white: #ffffff;
    --rule: #bdbdbd;
  }
  * { box-sizing: border-box; margin: 0; padding: 0; }
  html, body { width: 702px; height: 1200px; overflow: hidden; }
  body {
    background: radial-gradient(ellipse at 50% 30%, var(--stage-light), var(--stage) 70%);
    font-family: "Poppins", sans-serif;
    color: var(--white);
    position: relative;
  }

  /* ---------- shared panel pieces ---------- */
  .panel { position: absolute; overflow: hidden; }
  .panel--black { background: var(--bag); }
  .panel--orange { background: var(--orange); }

  .dot-field {
    position: absolute;
    border-radius: 50%;
    background: radial-gradient(circle, rgba(242,106,42,0.75) 0%, rgba(242,106,42,0.35) 45%, rgba(242,106,42,0) 70%);
  }
  .panel--orange .dot-field {
    background: radial-gradient(circle, rgba(255,160,90,0.55) 0%, rgba(255,160,90,0.2) 45%, rgba(255,160,90,0) 70%);
  }

  .quality-badge {
    position: absolute;
    width: 3.4em; height: 3.4em;
    border: 0.22em solid var(--white);
    border-radius: 50%;
  }

  .wordmark {
    position: absolute; left: 0; right: 0;
    text-align: center;
    font-family: "Montserrat", sans-serif;
    font-weight: 900;
    color: var(--orange);
    letter-spacing: 0.01em;
    line-height: 1;
  }

  .product-line {
    position: absolute;
    right: 11%;
    text-align: right;
    line-height: 1;
  }
  .product-line .coal {
    display: block;
    font-family: "Poppins", sans-serif;
    font-weight: 400;
    font-size: 1.05em;
    margin-bottom: 0.2em;
  }
  .product-line .name {
    font-family: "Montserrat", sans-serif;
    font-weight: 800;
    font-size: 1.5em;
    display: inline-flex; align-items: center; gap: 0.35em;
  }
  .pill {
    background: var(--orange);
    color: var(--ink);
    font-family: "Poppins", sans-serif;
    font-weight: 500;
    padding: 0.08em 0.3em;
    border-radius: 0.25em;
  }

  .rule {
    position: absolute; left: 13%; right: 11%;
    height: 0.12em; background: var(--rule);
  }
  .languages {
    position: absolute; left: 0; right: 0;
    text-align: center;
    font-family: "Barlow Condensed", sans-serif;
    font-weight: 300;
    font-size: 1.3em;
    line-height: 1.55;
  }
  .claim-band {
    position: absolute; left: 13%; right: 11%;
    background: var(--orange-soft);
    text-align: center;
    font-size: 0.7em;
    font-weight: 400;
    line-height: 1.55;
    padding: 0.35em 0;
  }

  .weight-stamp {
    position: absolute;
    width: 5.4em; height: 5.4em;
    border-radius: 50%;
    background: var(--white);
    display: flex; align-items: center; justify-content: center;
  }
  .weight-stamp .inner {
    width: 4.4em; height: 4.4em;
    border-radius: 50%;
    background: var(--ink);
    display: flex; flex-direction: column; align-items: center; justify-content: center;
    line-height: 1;
  }
  .weight-stamp .label { font-size: 0.55em; font-weight: 400; }
  .weight-stamp .value {
    font-family: "Barlow Condensed", sans-serif; font-weight: 400;
    font-size: 1.5em; margin-top: 0.1em;
  }

  /* side gusset: one block turned to read bottom-to-top */
  .gusset-type {
    position: absolute;
    left: var(--x);
    top: 100%;
    width: var(--len);
    padding-left: var(--lift);
    transform-origin: 0 0;
    transform: rotate(-90deg);
    line-height: 1;
  }
  .gusset-stack {
    display: inline-flex;
    flex-direction: column;
    align-items: flex-end;
  }
  .gusset-type .big {
    font-family: "Montserrat", sans-serif; font-weight: 900;
    color: var(--ink); font-size: 4.4em;
    white-space: nowrap;
  }
  .gusset-type .coal {
    color: var(--white);
    font-size: 0.95em;
    margin-top: 0.15em;
    white-space: nowrap;
  }
  .gusset-type .name {
    color: var(--white);
    font-family: "Montserrat", sans-serif; font-weight: 800;
    font-size: 1.25em; display: inline-flex; gap: 0.3em; align-items: center;
    margin-top: 0.15em;
    white-space: nowrap;
  }
  .gusset-type .pill { background: var(--ink); color: var(--orange); padding: 0.06em 0.3em; }

  /* ---------- flat front view ---------- */
  .front-view {
    position: absolute; left: 141px; top: 30px;
    width: 420px; height: 560px;
    box-shadow: 0 18px 30px rgba(120,40,0,0.35);
  }
  .front-view .face { left: 0; top: 0; width: 330px; height: 560px; font-size: 10px; }
  .front-view .side { left: 330px; top: 0; width: 90px; height: 560px; font-size: 10px; }

  /* ---------- dieline ---------- */
  .dieline {
    position: absolute; left: 22px; top: 632px;
    width: 658px; height: 537px;
    background: var(--ink);
  }
  .flap { position: absolute; background: var(--ink); border-right: 1px solid #333; }
  .flap--top { top: 0; height: 90px; border-bottom: 1px solid #333; }
  .flap--bottom { bottom: 0; height: 89px; border-top: 1px solid #333; }
  .dieline .panel { top: 90px; height: 358px; font-size: 7.2px; }
  .col-back  { left: 0;   width: 238px; }
  .col-side1 { left: 238px; width: 91px; }
  .col-front { left: 329px; width: 238px; }
  .col-side2 { left: 567px; width: 91px; }

  .warning {
    position: absolute; left: 13%; right: 11%;
    font-size: 0.78em; line-height: 1.45;
  }
  .warning-head {
    display: flex; align-items: center; gap: 0.5em;
    font-weight: 600; font-size: 1.05em; margin-bottom: 0.2em;
  }
  .warning-head svg { width: 1.3em; height: 1.3em; }
  .warning-head .note { font-weight: 400; font-size: 0.55em; line-height: 1.2; }
  .warning p { text-align: justify; }

  .handling-icons { position: absolute; left: 13%; display: flex; gap: 0.9em; }
  .handling-icons svg { width: 2.2em; height: 2.2em; }

  .batch { position: absolute; left: 13%; }
  .batch span { display: block; font-size: 0.55em; font-weight: 700; margin-bottom: 0.4em; }
  .batch i { display: block; width: 8.5em; height: 1.8em; background: var(--white); border-radius: 0.2em; }
</style>
</head>
<body>

  <!-- Flat front of the bag with side gusset -->
  <section class="front-view" aria-label="Vantrel 25 kg bag, front and side">
    <div class="panel panel--black face">
      <div class="dot-field" style="left:62%;top:-6%;width:55%;height:32%" role="img" aria-label="Orange dot arc pattern"></div>
      <div class="dot-field" style="left:-22%;top:56%;width:80%;height:52%" role="img" aria-label="Orange dot arc pattern"></div>
      <div class="quality-badge" style="left:7%;top:12%"></div>
      <div class="wordmark" style="top:32%;font-size:4.8em;padding-right:4%">VANTREL</div>
      <div class="product-line" style="top:41.5%"><span class="coal">COAL-BASED</span><span class="name"><span class="pill">PREMIUM</span>ACTIVATED CARBON</span></div>
      <div class="rule" style="top:50%"></div>
      <div class="languages" style="top:51.5%;padding-left:2%">活性炭 &nbsp;|&nbsp; Активированный уголь &nbsp;|&nbsp; كربون مفعل<br>Charbon actif &nbsp;|&nbsp; Geactiveerde koolstof</div>
      <div class="claim-band" style="top:62.5%">ORDERS AND IMPURITIES* FOR SPARKLING CLEAN WATER<br>IDEAL FOR ALL AQUARIUM FILTERS</div>
      <div class="weight-stamp" style="left:68%;top:84%"><div class="inner"><span class="label">Net Weight:</span><span class="value">25Kg</span></div></div>
    </div>
    <div class="panel panel--orange side">
      <div class="dot-field" style="left:-20%;top:-8%;width:140%;height:45%" role="img" aria-label="Light dot arc pattern"></div>
      <div class="gusset-type" style="--x:14px;--len:560px;--lift:70px">
        <div class="gusset-stack">
          <span class="big">VANTREL</span>
          <span class="coal">COAL-BASED</span>
          <span class="name"><span class="pill">PREMIUM</span>ACTIVATED CARBON</span>
        </div>
      </div>
    </div>
  </section>

  <!-- Flat dieline -->
  <section class="dieline" aria-label="Vantrel bag dieline">
    <div class="flap flap--top" style="left:0;width:238px"></div>
    <div class="flap flap--top" style="left:238px;width:91px"></div>
    <div class="flap flap--top" style="left:329px;width:238px"></div>
    <div class="flap flap--top" style="left:567px;width:91px;border-right:0"></div>
    <div class="flap flap--bottom" style="left:0;width:238px"></div>
    <div class="flap flap--bottom" style="left:238px;width:91px"></div>
    <div class="flap flap--bottom" style="left:329px;width:238px"></div>
    <div class="flap flap--bottom" style="left:567px;width:91px;border-right:0"></div>

    <!-- back panel -->
    <div class="panel panel--black col-back">
      <div class="dot-field" style="left:-22%;top:-12%;width:55%;height:50%" role="img" aria-label="Orange dot arc pattern"></div>
      <div class="dot-field" style="left:58%;top:62%;width:70%;height:60%" role="img" aria-label="Orange dot arc pattern"></div>
      <div class="wordmark" style="top:29%;font-size:3.6em;padding-right:2%">VANTREL</div>
      <div class="product-line" style="top:39%;right:25%;font-size:0.75em"><span class="coal">COAL-BASED</span><span class="name"><span class="pill">PREMIUM</span>ACTIVATED CARBON</span></div>
      <div class="rule" style="top:47.5%;right:45%;height:0.18em"></div>
      <div class="warning" style="top:49%">
        <div class="warning-head">
          <svg viewBox="0 0 20 20" aria-hidden="true"><path d="M10 2 L19 18 H1 Z" fill="none" stroke="#f26a2a" stroke-width="2"/><rect x="9" y="7.5" width="2" height="5" fill="#fff"/><rect x="9" y="14" width="2" height="2" fill="#fff"/></svg>
          <span>WARNING / CAUTION</span>
          <svg viewBox="0 0 20 20" aria-hidden="true"><rect x="4" y="4" width="12" height="12" transform="rotate(45 10 10)" fill="none" stroke="#fff" stroke-width="1.8"/><rect x="9.2" y="6" width="1.6" height="5.5" fill="#fff"/><rect x="9.2" y="12.5" width="1.6" height="1.6" fill="#fff"/></svg>
          <svg viewBox="0 0 20 20" aria-hidden="true"><rect x="4" y="4" width="12" height="12" transform="rotate(45 10 10)" fill="none" stroke="#fff" stroke-width="1.8"/><circle cx="10" cy="10" r="3" fill="#fff"/></svg>
          <span class="note">Harmful if inhaled.<br>Eye irritant</span>
        </div>
        <p>Activated carbon affects the respiratory and cardiovascular system. Wet activated carbon can deplete oxygen from the air creating dangerously low levels of oxygen in confined spaces. Please pay attention to working in confined spaces.</p>
      </div>
      <div class="handling-icons" style="top:67%">
        <svg viewBox="0 0 24 24" aria-label="Handle with care"><rect x="1" y="1" width="22" height="22" rx="2" fill="none" stroke="#fff" stroke-width="1.4"/><path d="M7 13 Q12 19 17 13" fill="none" stroke="#fff" stroke-width="1.6"/><rect x="9" y="6" width="6" height="6" fill="#fff"/></svg>
        <svg viewBox="0 0 24 24" aria-label="Keep dry"><rect x="1" y="1" width="22" height="22" rx="2" fill="none" stroke="#fff" stroke-width="1.4"/><path d="M5 12 Q12 3 19 12 Z" fill="#fff"/><path d="M12 12 V18 Q12 20 10 19" fill="none" stroke="#fff" stroke-width="1.4"/></svg>
        <svg viewBox="0 0 24 24" aria-label="Keep away from heat"><rect x="1" y="1" width="22" height="22" rx="2" fill="none" stroke="#fff" stroke-width="1.4"/><circle cx="12" cy="12" r="3" fill="#fff"/><path d="M12 4V7M12 17V20M4 12H7M17 12H20M6 6L8 8M16 16L18 18M6 18L8 16M16 8L18 6" stroke="#fff" stroke-width="1.3"/></svg>
        <svg viewBox="0 0 24 24" aria-label="No hooks"><rect x="1" y="1" width="22" height="22" rx="2" fill="none" stroke="#fff" stroke-width="1.4"/><path d="M12 4V14Q12 19 8 17" fill="none" stroke="#fff" stroke-width="1.6"/><path d="M6 6L18 18" stroke="#fff" stroke-width="1.3"/></svg>
        <svg viewBox="0 0 24 24" aria-label="Recyclable"><rect x="1" y="1" width="22" height="22" rx="2" fill="none" stroke="#fff" stroke-width="1.4"/><path d="M12 5L17 14H7Z" fill="none" stroke="#fff" stroke-width="1.6"/><path d="M6 18H18" stroke="#fff" stroke-width="1.6"/></svg>
      </div>
      <div class="batch" style="top:86%"><span>BATCH NUMBER</span><i></i></div>
    </div>

    <!-- left side gusset -->
    <div class="panel panel--orange col-side1">
      <div class="dot-field" style="left:-25%;top:58%;width:150%;height:55%" role="img" aria-label="Light dot arc pattern"></div>
      <div class="gusset-type" style="--x:14px;--len:358px;--lift:136px">
        <div class="gusset-stack">
          <span class="big">VANTREL</span>
          <span class="coal">COAL-BASED</span>
          <span class="name"><span class="pill">PREMIUM</span>ACTIVATED CARBON</span>
        </div>
      </div>
    </div>

    <!-- front panel -->
    <div class="panel panel--black col-front">
      <div class="dot-field" style="left:62%;top:-12%;width:55%;height:40%" role="img" aria-label="Orange dot arc pattern"></div>
      <div class="dot-field" style="left:-22%;top:60%;width:80%;height:60%" role="img" aria-label="Orange dot arc pattern"></div>
      <div class="quality-badge" style="left:11%;top:14%;font-size:0.8em"></div>
      <div class="wordmark" style="top:29%;font-size:4.5em;padding-right:2%">VANTREL</div>
      <div class="product-line" style="top:40%"><span class="coal">COAL-BASED</span><span class="name"><span class="pill">PREMIUM</span>ACTIVATED CARBON</span></div>
      <div class="rule" style="top:48.5%"></div>
      <div class="languages" style="top:50%;font-size:1.15em">活性炭 &nbsp;|&nbsp; Активированный уголь &nbsp;|&nbsp; كربون مفعل<br>Charbon actif &nbsp;|&nbsp; Geactiveerde koolstof</div>
      <div class="claim-band" style="top:62%;background:var(--orange);font-size:0.6em">ORDERS AND IMPURITIES* FOR SPARKLING CLEAN WATER<br>IDEAL FOR ALL AQUARIUM FILTERS</div>
      <div class="weight-stamp" style="left:68%;top:83%;font-size:0.75em"><div class="inner"><span class="label">Net Weight:</span><span class="value">25Kg</span></div></div>
    </div>

    <!-- right side gusset -->
    <div class="panel panel--orange col-side2">
      <div class="dot-field" style="left:-25%;top:-10%;width:150%;height:50%" role="img" aria-label="Light dot arc pattern"></div>
      <div class="gusset-type" style="--x:14px;--len:358px;--lift:70px">
        <div class="gusset-stack">
          <span class="big">VANTREL</span>
          <span class="coal">COAL-BASED</span>
          <span class="name"><span class="pill">PREMIUM</span>ACTIVATED CARBON</span>
        </div>
      </div>
    </div>
  </section>

</body>
</html>
```